Core Value Graphic for a Service Disabled and Minority Certified contractor

My company, Keystone Aid Partners, is a US Federal Contractor that hires veterans and service disabled veterans. Our website is www.keystoneaid7.example. We work hard to maintain a 50:50 split between veterans and non-veterans on our team. Our tagline is "To Find a Better Way." We are continually looking to integrate technology and efficiency into all that we do.

I want a way to express our company core values visually so that our employees and customers alike can read them and get a sense of who we are, what drives us to succeed, and what makes up our team DNA.

I need an artist like you to help me represent our core values visually. In a manner that I can print it out on an 8"X11" sheet of paper or a large 48" X 48" poster, without losing the visual clarity or that it pixelates out of focus. I am looking for a color scheme that is patriotic with Red, White, and Blues and similar hues. I would also like to incorporate my logo and tagline into the design in some manner.

I have attached several examples of a Core Value Grids from other companies. I am hopeful it will inspire you, and a get your brain juices flowing to provide me with a knockout Core Value Grid that will rock only you can provide! I also include a copy of my company Core Values and a copy of our Logo.

Looking forward to seeing your creations. Thanks.

Target Market(s)

Employees, any potential strategic alliance partners, and customers.

Industry/Entity Type

Contractor

Requirements
Must have
• Patriotic feel and have my logo someplace on the document.

```html
<!DOCTYPE html>
<html lang="en">
<head>
<meta charset="utf-8">
<title>Core Values – Keystone Aid Partners</title>
<link href="https://fonts.googleapis.com/css2?family=Exo+2:wght@500;600&family=Montserrat:wght@700;800&family=Roboto:wght@400;500&family=Roboto+Condensed:wght@400&display=swap" rel="stylesheet">
<style>
  :root{
    --page-bg:#e6e6e6;
    --crimson:#b21d36;
    --wine:#5b0e1c;
    --navy:#1a2457;
    --white:#ffffff;
    --ink-soft:#f3e6e8;
    --logo-red:#c8202f;
  }
  html,body{margin:0;padding:0;width:1118px;height:1200px;overflow:hidden;background:var(--page-bg);}
  .poster{
    position:absolute;left:261px;top:178px;width:595px;height:842px;overflow:hidden;
    background:radial-gradient(ellipse 75% 60% at 55% 52%,var(--crimson) 0%,#8b1529 55%,var(--wine) 100%);
    color:var(--white);font-family:"Roboto",sans-serif;
  }
  .connectors{position:absolute;left:0;top:0;width:595px;height:842px;}
  .value{position:absolute;}
  .value h2{margin:0;font-weight:500;line-height:1.15;}
  .value--top h2{font-family:"Exo 2",sans-serif;font-weight:600;font-size:18px;}
  .value--low h2{font-family:"Roboto",sans-serif;font-size:17.5px;}
  .value p{margin:0;text-align:justify;color:var(--ink-soft);}
  .value--top p{font-family:"Roboto Condensed",sans-serif;font-size:7.6px;line-height:11.5px;text-indent:9px;}
  .value--low p{font-size:8.2px;line-height:12px;text-indent:9px;margin-bottom:3px;}
  .value--wide p{text-indent:0;}
  .tagline{position:absolute;left:85px;width:426px;text-align:center;font-family:"Montserrat",sans-serif;font-weight:800;letter-spacing:1px;}
  .tagline--main{top:266px;font-size:35px;}
  .tagline--sub{top:315px;font-size:22px;font-weight:700;}
  .banner-title{position:absolute;left:112px;top:364px;width:372px;height:68px;line-height:68px;text-align:center;font-family:"Montserrat",sans-serif;font-weight:800;font-size:41px;letter-spacing:1px;}
  .site{position:absolute;left:26px;top:797px;font-size:13px;font-family:"Roboto",sans-serif;}
  .footer-band{position:absolute;left:0;bottom:0;width:595px;height:21px;background:var(--navy);}
  .brand{position:absolute;left:424px;top:771px;width:140px;height:58px;background:var(--white);display:flex;align-items:center;justify-content:center;gap:6px;}
  .brand-mark{width:10px;height:10px;background:var(--logo-red);}
  .brand-name{font-family:"Roboto",sans-serif;font-weight:500;font-size:11px;color:var(--logo-red);}
</style>
</head>
<body>
<main class="poster">
  <svg class="connectors" viewBox="0 0 595 842" aria-hidden="true">
    <g fill="none" stroke="#fff" stroke-width="1.3">
      <path d="M29 58 V265 H85"/>
      <path d="M519 60 H566 V265 H511"/>
      <path d="M85 321 H29 V670"/>
      <path d="M85 376 H49 V482"/>
      <path d="M511 376 H566 V482 H494"/>
      <path d="M124 400 H94 Q85 400 85 391 V255 Q85 246 94 246 H502 Q511 246 511 255 V391 Q511 400 502 400 H473"/>
    </g>
    <g fill="#fff">
      <circle cx="29" cy="58" r="3"/><circle cx="519" cy="60" r="3"/>
      <circle cx="29" cy="670" r="3"/><circle cx="49" cy="482" r="3"/><circle cx="494" cy="482" r="3"/>
    </g>
    <polygon points="112,364 484,364 472,398 484,432 112,432 124,398" fill="var(--navy)"/>
  </svg>

  <section class="value value--top" style="left:54px;top:47px;width:238px;">
    <h2>Everyone comes back to<br>the Green Zone.</h2>
    <div style="margin-top:12px">
      <p>WHAT IT MEANS- Safety takes precedence over every phase of the day's operation.</p>
      <p>HOW TO EXPRESS IT - Anyone can call a stop to the work in progress if an unsafe act is occurring. In fact, it is each team member's duty to do so, rectify the unsafe issue, then proceed. Never hesitate; everyone comes back. Finally, each After Action Review begins with discussing safety issues.</p>
      <p>We always let everyone on the team know of an unsafe situation, so it can be avoided in the future.</p>
      <p>RESULT - All team members go home to their loved ones each day to pursue their individual happiness.</p>
    </div>
  </section>

  <section class="value value--top" style="left:318px;top:51px;width:239px;">
    <h2>Boldly go. Seek. Find.</h2>
    <div style="margin-top:17px">
      <p>WHAT IT MEANS: - We weave innovation into the fabric that makes up our company.</p>
      <p>HOW TO EXPRESS IT: - We're early adopters of technology. We quickly evaluate new technologies or processes that could separate us from our competition. Then we implement and evaluate these new technologies. We dump it quickly if we see it is not helping us achieve "Commander's Intent." We have the guts to be first. We iterate continuously and attack, attack, attack.</p>
      <p>RESULT: - We will be ahead of our competition. It' one mechanism that helps us scale. Prosperity favors the bold!</p>
    </div>
  </section>

  <div class="tagline tagline--main">TO FIND</div>
  <div class="tagline tagline--sub">A BETTER WAY</div>
  <div class="banner-title">CORE VALUES</div>

  <section class="value value--low" style="left:44px;top:470px;width:236px;">
    <h2 style="padding-left:14px">Never leave your wingman</h2>
    <div style="margin-top:12px">
      <p>WHAT IT MEANS – We always help your team members be successful. Commitment to each other and to our own personal integrity is the fuel that empowers us.</p>
      <p>HOW TO EXPRESS IT – If a Wingman is having challenges accomplishing their individual priorities or completing their assigned mission, volunteer to help them to do so.</p>
      <p>This goes for Subs/Suppliers as well. We help those who help us succeed! Always look to establish the best win-win relationship possible, and do what you can to support them if they get into a bind.</p>
      <p>RESULT – Be there for them and they will be there for us.</p>
    </div>
  </section>

  <section class="value value--low" style="left:302px;top:470px;width:237px;">
    <h2 style="padding-left:6px">Fail quickly and learn</h2>
    <div style="margin-top:12px">
      <p>WHAT IT MEANS – If you're not making mistakes, you're not taking enough chances or getting out of your comfort zone.</p>
      <p>HOW TO EXPRESS IT – Use your best judgment when trying something new. But, don't let your pride keep you from saying, "I was wrong" when your idea doesn't work. We trust you will know when it's time to dump the idea, or stop doing something that doesn't work.</p>
      <p>RESULT – No one will ever be penalized for making a mistake. Don't be afraid to try something you believe will work. That's how we grow ourselves and our team members.</p>
    </div>
  </section>

  <section class="value value--low value--wide" style="left:44px;top:660px;width:495px;">
    <h2>Troops (Team Members)&nbsp; eat first</h2>
    <div style="margin-top:13px">
      <p>WHAT IT MEANS – No leader will put themselves ahead of their subordinates.</p>
      <p>HOW TO EXPRESS IT – We lead by example. Demonstrate the moral courage and discipline to do the right thing at the highest level of quality.</p>
      <p>RESULT – Every new teammember's will quickly realize their leaders genuinely care for their welfare and success. This is the best way to drive Esprit de Corps and achieve excellence.</p>
    </div>
  </section>

  <div class="site">www.keystoneaid7.example</div>
  <div class="footer-band"></div>
  <div class="brand"><span class="brand-mark"></span><span class="brand-name">Keystone Aid Partners</span></div>
</main>
</body>
</html>
```